Irrigation Business needs their business cards modernised and revamped

I would like to keep my current logo, colours and revamp the format of the card.

I would like the card to be clean yet important.

Im not sure if you include texture but i would like the named logo to be indented into the card etc.

show me something alive and free something thats clinical to the point yet has a feel of achievement. i would like people to go nice card.

Target Market(s)

high end clients, corporate, sports field manger, the guys that make the decisions

Industry/Entity Type

Business

Contact Information for Business Card

nformation to be included

Dean Harlow (Director)
0487305526
dean@kolvat.biz
www.kestonfieldworks.com

instagram logo
google logo
facebook logo

Colors

Designer to choose colors to be used in the design.

Requirements
Nice to have
• indentations a really nice feel to the card good texture

```html
<!DOCTYPE html>
<html lang="en">
<head>
<meta charset="utf-8">
<title>Keston Fieldworks – Business Card</title>
<link href="https://fonts.googleapis.com/css2?family=Montserrat:wght@400;500;600;700&display=swap" rel="stylesheet">
<style>
  :root {
    --backdrop: #2a2a2a;
    --card-white: #ffffff;
    --brand-blue: #2a5ea8;
    --brand-blue-text: #2b5fa6;
    --ink-grey: #6d6d6d;
    --muted-grey: #8a8a8a;
    --accent-teal: #3aa7c9;
    --ghost: rgba(0, 0, 0, 0.035);
  }
  * { margin: 0; padding: 0; box-sizing: border-box; }
  html, body {
    width: 1200px;
    height: 674px;
    overflow: hidden;
    background: var(--backdrop);
    font-family: "Montserrat", Arial, sans-serif;
  }
  .canvas {
    position: relative;
    width: 1200px;
    height: 674px;
  }
  .card {
    position: absolute;
    top: 244px;
    width: 328px;
    height: 187px;
    border-radius: 11px;
    overflow: hidden;
  }
  .card-front { left: 267px; background: var(--card-white); }
  .card-back { left: 605px; background: var(--brand-blue); }

  .ghost-ring {
    position: absolute;
    left: 240px;
    top: 6px;
    width: 176px;
    height: 176px;
    border-radius: 50%;
    border: 14px solid var(--ghost);
  }

  .brand {
    position: absolute;
    display: flex;
    flex-direction: column;
    align-items: center;
  }
  .brand-dot {
    width: 34px;
    height: 34px;
    border-radius: 50%;
    background: var(--brand-blue);
    margin-bottom: 6px;
  }
  .brand-name {
    font-weight: 700;
    font-size: 10.5px;
    line-height: 1.15;
    letter-spacing: 0.2px;
    text-align: center;
    color: var(--brand-blue-text);
    text-transform: uppercase;
  }
  .card-front .brand { left: 18px; top: 16px; width: 100px; }
  .card-back .brand { right: 20px; bottom: 20px; width: 120px; }
  .card-back .brand-dot { background: var(--card-white); }
  .card-back .brand-name { color: var(--card-white); }

  .holder { position: absolute; left: 20px; top: 105px; }
  .holder-name {
    font-weight: 600;
    font-size: 10.5px;
    color: var(--brand-blue-text);
  }
  .holder-role {
    font-size: 7.5px;
    color: var(--ink-grey);
    margin-top: 1px;
  }
  .holder-rule {
    width: 10px;
    height: 1.5px;
    background: var(--accent-teal);
    margin-top: 6px;
  }

  .contact-list {
    position: absolute;
    left: 20px;
    top: 141px;
    list-style: none;
  }
  .contact-list li {
    display: flex;
    align-items: center;
    height: 10.5px;
    font-size: 7px;
    color: var(--muted-grey);
    letter-spacing: 0.2px;
  }
  .contact-list svg {
    width: 6px;
    height: 6px;
    margin-right: 8px;
    fill: var(--brand-blue);
  }
  .contact-list .web { color: var(--brand-blue-text); }

  .social-row {
    position: absolute;
    left: 175px;
    top: 163px;
    display: flex;
    gap: 3px;
  }
  .social-dot {
    width: 8px;
    height: 8px;
    border-radius: 2px;
    background: var(--brand-blue);
  }
</style>
</head>
<body>
<main class="canvas">
  <section class="card card-front">
    <div class="ghost-ring"></div>

    <div class="brand">
      <div class="brand-dot"></div>
      <div class="brand-name">Keston<br>Fieldworks</div>
    </div>

    <div class="holder">
      <div class="holder-name">Dean Harlow</div>
      <div class="holder-role">Director</div>
      <div class="holder-rule"></div>
    </div>

    <ul class="contact-list">
      <li>
        <svg viewBox="0 0 10 10" aria-hidden="true"><path d="M2.2 0.5 L3.8 2.6 L2.9 3.7 Q4 6 6.3 7.1 L7.4 6.2 L9.5 7.8 L8.4 9.5 Q3.6 9 0.5 1.6 Z"/></svg>
        0487305526
      </li>
      <li>
        <svg viewBox="0 0 10 10" aria-hidden="true"><path d="M0.5 2 H9.5 V8.5 H0.5 Z M0.5 2 L5 5.6 L9.5 2" fill="none" stroke="#2a5ea8" stroke-width="1.2"/></svg>
        dean@kolvat.biz
      </li>
      <li class="web">
        <svg viewBox="0 0 10 10" aria-hidden="true"><g fill="none" stroke="#2a5ea8" stroke-width="0.9"><circle cx="5" cy="5" r="4.3"/><ellipse cx="5" cy="5" rx="1.8" ry="4.3"/><path d="M0.7 5 H9.3"/></g></svg>
        www.kestonfieldworks.com
      </li>
    </ul>

    <div class="social-row" aria-label="Social profiles">
      <span class="social-dot"></span>
      <span class="social-dot"></span>
      <span class="social-dot"></span>
    </div>
  </section>

  <section class="card card-back">
    <div class="brand">
      <div class="brand-dot"></div>
      <div class="brand-name">Keston<br>Fieldworks</div>
    </div>
  </section>
</main>
</body>
</html>
```